Tellmora Corporate Stationery

Look for design of all new corporate stationery for an existing insurance broking business that is going through a redesign and move from older partners to younger family members. New Logo is attached. Company is Brisbane based.
Colours in the Logo is Hex #43bed8 and website features a lot of hex #17b8d8. Website front page "A plan to protect you" - headline. "Professional and Individual advice to protect your greatest assets" - tagline.

Stationery required: Business Cards, Letter head, Thank-you cards, Birthday cards, Presentation folders, With Compliment slips and a powerpoint template. We also would like to send a card to all customers with the something along of the lines of "something new".

Target Market(s)

Customers of Insurance business looking at superannuation, life and income protection insurance, investment advice and wills

Industry/Entity Type

Insurance Broker

Font styles to use
Other font styles liked:
• same as logo

Requirements
Must have
• The above designs for new stationery for the new business including:
• Business Cards, Letter head, Thank-you cards, Birthday cards, Presentation folders, With Compliment slips and a powerpoint template. We also would like to send a card to all customers with the something along of the lines of "something new".
Nice to have
• It is a new look - long time family business being passed to next generation - big focus on advice for YOU, individual advice etc..

```html
<!DOCTYPE html>
<html lang="en">
<head>
<meta charset="utf-8">
<title>Tellmora Business Card</title>
<link rel="stylesheet" href="https://fonts.googleapis.com/css2?family=Source+Sans+3:ital,wght@0,400;0,600;1,400&display=swap">
<style>
  :root {
    --backdrop: #1f1f20;
    --card-white: #ffffff;
    --brand-cyan: #43bed8;
    --brand-cyan-soft: #4cc6de;
    --text-grey: #5a5a5c;
    --label-grey: #7d7d80;
    --divider: #d6d6d6;
  }
  * { box-sizing: border-box; margin: 0; padding: 0; }
  html, body {
    width: 1200px; height: 987px; overflow: hidden;
    background: var(--backdrop);
    font-family: "Source Sans 3", "Helvetica Neue", Arial, sans-serif;
  }
  .stage { position: relative; width: 1200px; height: 987px; }
  .card {
    position: absolute; left: 293px; width: 615px; height: 352px;
  }
  .card-front { top: 130px; background: var(--card-white); }
  .card-back { top: 505px; background: var(--brand-cyan); overflow: hidden; }

  .brand-lockup {
    position: absolute; left: 0; width: 325px; top: 0; height: 352px;
    display: flex; align-items: center; justify-content: center; gap: 12px;
  }
  .brand-dot {
    width: 26px; height: 26px; border-radius: 50%; background: var(--brand-cyan);
  }
  .brand-name {
    font-weight: 600; font-size: 36px; letter-spacing: 2px; color: var(--brand-cyan);
    text-transform: uppercase;
  }
  .divider {
    position: absolute; left: 325px; top: 58px; width: 1px; height: 240px; background: var(--divider);
  }
  .contact-block { position: absolute; left: 352px; top: 58px; color: var(--text-grey); }
  .person-name {
    font-weight: 600; font-size: 24px; color: var(--brand-cyan); letter-spacing: 0.3px; line-height: 1;
  }
  .person-role { font-size: 16px; color: var(--label-grey); margin-top: 5px; }
  .address { font-size: 16px; line-height: 23px; margin-top: 11px; }
  .contact-list { list-style: none; margin-top: 6px; }
  .contact-list li {
    display: flex; align-items: center; gap: 8px; font-size: 16px; line-height: 23.5px;
  }
  .contact-list svg { width: 16px; height: 16px; flex: none; fill: var(--brand-cyan); }

  .back-pattern {
    position: absolute; inset: 0;
    background: linear-gradient(135deg, var(--brand-cyan-soft), var(--brand-cyan));
  }
  .back-mark {
    position: absolute; left: 0; right: 0; top: 148px;
    display: flex; align-items: center; justify-content: center; gap: 10px;
  }
  .back-mark .brand-dot { background: var(--card-white); width: 22px; height: 22px; }
  .back-mark .brand-name { color: var(--card-white); font-size: 30px; }
  .back-web {
    position: absolute; left: 0; right: 0; top: 288px; text-align: center;
    color: var(--card-white); font-style: italic; font-size: 17px; letter-spacing: 2px;
  }
</style>
</head>
<body>
<main class="stage">
  <section class="card card-front">
    <div class="brand-lockup">
      <span class="brand-dot"></span>
      <span class="brand-name">Tellmora</span>
    </div>
    <div class="divider"></div>
    <div class="contact-block">
      <p class="person-name">LIAM CARTER</p>
      <p class="person-role">CEO/FOUNDER</p>
      <p class="address">214 Wattle Grove Road<br>Brisbane, Queensland 4000</p>
      <ul class="contact-list">
        <li><svg viewBox="0 0 16 16"><path d="M3.5 1.5l2.5 0 1 3.5-1.8 1.2c.8 1.8 2.2 3.2 4 4L10.4 8.4l3.6 1v2.6c0 1-1 2-2 2C6.8 14 2 9.2 2 3.5c0-1 .6-2 1.5-2z"/></svg>617 302 4815</li>
        <li><svg viewBox="0 0 16 16"><path d="M5 1h6a1 1 0 0 1 1 1v12a1 1 0 0 1-1 1H5a1 1 0 0 1-1-1V2a1 1 0 0 1 1-1zm.6 1.6v9.4h4.8V2.6zM8 12.6a.8.8 0 1 0 0 1.6.8.8 0 0 0 0-1.6z"/></svg>0412 583 907</li>
        <li><svg viewBox="0 0 16 16"><path d="M4 1h8v4H4zM1.5 6h13a1 1 0 0 1 1 1v5h-2v3h-11v-3h-2V7a1 1 0 0 1 1-1zm2.5 5v3h8v-3z"/></svg>617 302 4816</li>
        <li><svg viewBox="0 0 16 16"><path d="M1 3.5h14v9H1zm1.4 1.2L8 8.6l5.6-3.9z"/></svg>liam@tellmora.com</li>
        <li><svg viewBox="0 0 16 16"><path d="M8 1a7 7 0 1 0 0 14A7 7 0 0 0 8 1zm-1 2.2c-.6.8-1.8 1-2.2 2.2.8.4 1.6 0 2 .9.3.9-.7 1.5 0 2.5.6.8 1.6.2 1.8 1.4.1 1-.5 2 .1 2.6A5.6 5.6 0 0 0 13.4 8c-.9-.2-1.5-1.2-2.5-.9-.8.2-1.4-.6-1-1.3.5-.9 1.7-.8 1.8-1.8A5.6 5.6 0 0 0 7 3.2z"/></svg>www.tellmora.com</li>
      </ul>
    </div>
  </section>

  <section class="card card-back">
    <div class="back-pattern" role="img" aria-label="Repeating faint brand pattern across the cyan card back"></div>
    <div class="back-mark">
      <span class="brand-dot"></span>
      <span class="brand-name">Tellmora</span>
    </div>
    <p class="back-web">www.tellmora.com</p>
  </section>
</main>
</body>
</html>
```